BOLD & MINIMALIST DESIGN NEEDED

We want a very bold but minimalistic business card design that is impactful and utilizes both sides of the business card. Our current logo is included for your use.

We want bold fonts and good use of negative space. We don't want the logo to overpower the design.

Target Market(s)

Professionals who are building new commercial buildings.

Industry/Entity Type

Construction

Contact Information for Business Card

Name, Title, email, office phone, cell phone, website

Font styles to use
Serif
Sans Serif

Requirements
Must have
• Bold design!

```html
<!DOCTYPE html>
<html lang="en">
<head>
<meta charset="utf-8">
<title>Crestline Design + Build — Business Card</title>
<link rel="stylesheet" href="https://fonts.googleapis.com/css2?family=Open+Sans:wght@400;600;800&display=swap">
<style>
  :root {
    --bg: #ececec;
    --ink: #141414;
    --card-black: #0d0d0d;
    --paper: #ffffff;
    --green: #7cc242;
    --grey: #5a5a5a;
    --light: #f2f2f2;
  }
  * { box-sizing: border-box; margin: 0; padding: 0; }
  html, body { width: 1200px; height: 900px; overflow: hidden; background: var(--bg); }
  body { font-family: "Open Sans", Arial, sans-serif; position: relative; }

  .card {
    position: absolute;
    left: 320px;
    width: 560px;
    height: 320px;
    border-radius: 24px;
    overflow: hidden;
    box-shadow: 0 10px 30px rgba(0,0,0,0.18);
  }
  .card--front { top: 95px; background: var(--paper); }
  .card--back { top: 485px; background: radial-gradient(ellipse at 70% 40%, #2a2a2a 0%, var(--card-black) 70%); }

  .front-shape { position: absolute; inset: 0; width: 100%; height: 100%; }

  .wordmark {
    display: flex;
    align-items: center;
    gap: 10px;
    font-weight: 800;
    text-transform: uppercase;
    letter-spacing: 0.5px;
  }
  .wordmark__mark { width: 16px; height: 16px; background: var(--green); flex: none; }
  .wordmark__name { font-size: 22px; }

  .card--front .wordmark { position: absolute; left: 34px; top: 34px; color: var(--ink); }

  .contact-list { position: absolute; left: 34px; top: 92px; list-style: none; }
  .contact-list li {
    display: flex; align-items: center; gap: 8px;
    font-size: 13px; color: var(--grey); line-height: 23px;
  }
  .contact-list svg { width: 13px; height: 13px; flex: none; }

  .person { position: absolute; right: 34px; top: 120px; text-align: right; }
  .person__name { font-size: 19px; font-weight: 600; color: var(--green); text-transform: uppercase; letter-spacing: 1px; }
  .person__title { font-size: 14px; color: var(--grey); margin-top: 2px; }

  .accent-block { position: absolute; right: 70px; bottom: 40px; width: 64px; height: 64px; background: var(--green); }

  .address {
    position: absolute; left: 34px; bottom: 28px;
    font-size: 14px; line-height: 20px; color: var(--light);
  }

  .card--back .wordmark {
    position: absolute; left: 50%; top: 50%;
    transform: translate(-50%, -50%);
    color: var(--paper);
  }
  .card--back .wordmark__name { font-size: 28px; }
</style>
</head>
<body>

  <section class="card card--front" aria-label="Card front">
    <svg class="front-shape" viewBox="0 0 560 320" preserveAspectRatio="none" aria-hidden="true">
      <path d="M0 170 C 120 200, 200 260, 300 250 C 380 242, 420 300, 440 320 L0 320 Z" fill="var(--card-black)"/>
      <path d="M0 150 C 110 175, 190 240, 290 232" fill="none" stroke="var(--green)" stroke-width="5" stroke-linecap="round"/>
    </svg>

    <div class="wordmark">
      <span class="wordmark__mark"></span>
      <span class="wordmark__name">Crestline Design + Build</span>
    </div>

    <ul class="contact-list">
      <li>
        <svg viewBox="0 0 12 12"><circle cx="6" cy="6" r="6" fill="var(--green)"/><path d="M4 3.2 L5 4.6 L4.6 5.2 C5 6 5.8 6.8 6.6 7.2 L7.2 6.8 L8.6 7.8 L8 8.8 C6 8.6 3.4 6 3.2 4 Z" fill="#fff"/></svg>
        055-210 384 617
      </li>
      <li>
        <svg viewBox="0 0 12 12"><circle cx="6" cy="6" r="6" fill="var(--green)"/><rect x="3" y="4" width="6" height="4.2" fill="#fff"/><path d="M3 4 L6 6.4 L9 4" fill="none" stroke="var(--green)" stroke-width="0.8"/></svg>
        hello@crestlinebuild.com
      </li>
      <li>
        <svg viewBox="0 0 12 12"><circle cx="6" cy="6" r="6" fill="var(--green)"/><circle cx="6" cy="6" r="3" fill="none" stroke="#fff" stroke-width="0.9"/><path d="M3 6 H9 M6 3 V9" stroke="#fff" stroke-width="0.8"/></svg>
        www.crestlinebuild.com
      </li>
    </ul>

    <div class="person">
      <p class="person__name">Marcus Hale</p>
      <p class="person__title">Managing Director</p>
    </div>

    <div class="accent-block" aria-hidden="true"></div>

    <p class="address">Your Address, City<br>State, Zip 0000</p>
  </section>

  <section class="card card--back" aria-label="Card back">
    <div class="wordmark">
      <span class="wordmark__mark"></span>
      <span class="wordmark__name">Crestline Design + Build</span>
    </div>
  </section>

</body>
</html>
```